Business card design for Automotive workshop

We need a business card for a new automotive repair and tyre shop called Keelstone Prime Automotive located in New Zealand. We are a clean, modern and fresh workshop and company.

Front needs to feature logo,
my name:
Marlo Fenwicke (director)

Address:
48 Tarn Lane
Whitianga 3510

Phone: 07 594 2713
Mobile: 027 451 9362
Email: office@keelstoneautomotive.example.nz
Website: keelstoneautomotive.example.nz

Back needs to feature an area to write down appointment details, date and time.

Also feature a list of jobs and work we do such as,
Vehicle Servicing
All Mechanical Repairs
Warrant of Fitness
Tyres & Wheel Alignments
Automotive Diagnostics
Automotive Parts & Supplies

```html
<!DOCTYPE html>
<html lang="en">
<head>
<meta charset="utf-8">
<title>Keelstone Prime Automotive – Business Card</title>
<link href="https://fonts.googleapis.com/css2?family=Lato:wght@400;700&family=Oswald:wght@500&display=swap" rel="stylesheet">
<style>
  :root {
    --stage: #1c1c1c;
    --card-light: #ffffff;
    --card-dark: #1f1f1f;
    --card-dark-edge: #2a2a2a;
    --accent: #e3242b;
    --ink: #3a3a3a;
    --ink-soft: #6a6a6a;
    --paper-text: #f2f2f2;
  }
  * { box-sizing: border-box; margin: 0; padding: 0; }
  html, body {
    width: 1200px; height: 900px; overflow: hidden;
    background: var(--stage);
    font-family: "Lato", sans-serif;
  }
  .canvas {
    width: 1200px; height: 900px;
    display: flex; flex-direction: column; align-items: center; justify-content: center;
    gap: 40px;
  }
  .card {
    width: 660px; height: 377px; position: relative; overflow: hidden;
    box-shadow: 0 18px 40px rgba(0,0,0,.55);
  }

  /* Appointment side */
  .card--appointment { background: var(--card-light); color: var(--ink); padding: 42px 48px 0; }
  .brand {
    text-align: center; color: var(--accent);
    font-weight: 700; font-size: 27px; letter-spacing: 2px; text-transform: uppercase;
    display: flex; align-items: center; justify-content: center; gap: 12px;
  }
  .brand__mark { width: 14px; height: 14px; background: var(--accent); }
  .appointment__title {
    text-align: center; color: var(--accent); font-size: 15px; margin-top: 34px;
  }
  .appointment__fields { margin-top: 4px; font-size: 14px; color: var(--ink-soft); }
  .field { display: flex; align-items: flex-end; gap: 4px; }
  .field__line { border-bottom: 1px solid var(--ink-soft); height: 14px; }
  .field--date .field__line { width: 260px; }
  .field--time { margin-top: 22px; margin-left: 304px; }
  .field--time .field__line { width: 250px; }
  .services { margin-top: 30px; text-align: center; font-size: 17px; line-height: 1.4; letter-spacing: .3px; }
  .services .sep { color: var(--accent); padding: 0 4px; }

  /* Contact side */
  .card--contact {
    background: radial-gradient(ellipse at 85% 40%, var(--card-dark-edge), var(--card-dark) 60%);
    color: var(--paper-text);
  }
  .person { position: absolute; left: 30px; width: 270px; top: 104px; text-align: right; }
  .person__name {
    font-family: "Oswald", sans-serif; font-weight: 500; color: var(--accent);
    font-size: 36px; letter-spacing: .5px; text-transform: uppercase; line-height: 1.1;
  }
  .person__role { font-size: 18px; margin-top: 2px; }
  .divider { position: absolute; left: 318px; top: 106px; width: 1px; height: 92px; background: var(--accent); }
  .contacts { position: absolute; left: 334px; top: 106px; list-style: none; font-size: 15px; line-height: 23px; }
  .contacts li { display: flex; align-items: center; gap: 7px; white-space: nowrap; }
  .contacts svg { width: 11px; height: 11px; flex: none; }
  .address { position: absolute; left: 0; right: 0; bottom: 48px; text-align: center; font-size: 20px; letter-spacing: .3px; }
</style>
</head>
<body>
<main class="canvas">
  <section class="card card--appointment">
    <div class="brand"><span class="brand__mark"></span>Keelstone Prime Automotive</div>
    <p class="appointment__title">Appointment</p>
    <div class="appointment__fields">
      <div class="field field--date">Date<span class="field__line"></span></div>
      <div class="field field--time">Time<span class="field__line"></span></div>
    </div>
    <div class="services">
      <p>Vehicle Servicing<span class="sep">|</span>All Mechanical Repairs</p>
      <p>Warrant of Fitness<span class="sep">|</span>Tyres &amp; Wheel Alignments</p>
      <p>Automotive Diagnostics<span class="sep">|</span>Automotive Parts &amp; Supplies</p>
    </div>
  </section>

  <section class="card card--contact">
    <div class="person">
      <h1 class="person__name">Marlo Fenwicke</h1>
      <p class="person__role">Director</p>
    </div>
    <div class="divider"></div>
    <ul class="contacts">
      <li><svg viewBox="0 0 12 12" fill="none" stroke="#e3242b" stroke-width="1.4"><path d="M2.5 1.5l2 2-1 1.5c.8 1.6 1.9 2.7 3.5 3.5l1.5-1 2 2-1.3 1.5C5 10.5 1.5 7 1 2.8z"/></svg>07 594 2713</li>
      <li><svg viewBox="0 0 12 12" fill="none" stroke="#e3242b" stroke-width="1.4"><rect x="3" y="1" width="6" height="10" rx="1"/><path d="M5.5 9h1"/></svg>027 451 9362</li>
      <li><svg viewBox="0 0 12 12" fill="none" stroke="#e3242b" stroke-width="1.4"><rect x="1" y="2.5" width="10" height="7"/><path d="M1 2.5l5 4 5-4"/></svg>office@keelstoneautomotive.example.nz</li>
      <li><svg viewBox="0 0 12 12" fill="none" stroke="#e3242b" stroke-width="1.2"><circle cx="6" cy="6" r="5"/><ellipse cx="6" cy="6" rx="2.2" ry="5"/><path d="M1 6h10"/></svg>www.keelstoneautomotive.example.nz</li>
    </ul>
    <p class="address">48 Tarn Lane Whitianga 3510</p>
  </section>
</main>
</body>
</html>
```